Quiet Harbor Coffee - Full Brand Packaging Suite (Pods, Boxes, Bags)

Quiet Harbor Coffee is commissioning a complete packaging system for our 12‑roast specialty coffee collection. Each roast is inspired by a Christian ministry, and every package must follow a consistent storytelling structure across all formats: single‑serve pod lids, 12‑count and 24‑count pod boxes, 12 oz bags, and 2 lb bags.Packaging Formats Needed:• Single‑Serve Pod Lids: Circular design featuring roast name, roast type, ministry inspiration, and color theme.
• 12‑Count & 24‑Count Pod Boxes: Full panel design (front, back, sides, top) matching the roast’s identity and ministry story.
• 12 oz Bag: Vertical layout with strong shelf presence, roast color theme, ministry spotlight, and brand story.
• 2 lb Bag: Same design language as the 12 oz bag, scaled appropriately.
Required Panel Structure (applies to every roast):• Front Panel:• Roast Name
• Roast Type
• “Inspired By: [Ministry Name]”
• “Mission Driven | Fueling Global Impact”
• “Brew it. Share it. Fuel the Mission.”

• Side A — Roast Story:
A short, emotionally resonant description connecting the roast’s flavor profile or theme to the ministry’s impact.
• Side B — Ministry Spotlight:
Ministry name, mission summary, and a “Scan to Give” callout with website link.
• Back Panel:• Flavor Notes
• Origin
• Quiet Harbor Coffee Story (provided text stays consistent across all roasts)
• Statement of giving: “50% of net proceeds support our ministry partners + 10% of gross sales from each roast go directly to the ministry it represents.”

Brand Identity:
Quiet Harbor Coffee blends premium specialty coffee with faith‑driven purpose. Designs should feel clean, premium, unified, and visually distinct per roast through color, tone, and ministry theme.Deliverables:• Print‑ready files for all packaging formats
• Editable source files
• Cohesive color system across all 12 roasts
• Consistent layout structure across lids, boxes, and bags
Goal:
Create a unified, premium packaging system that elevates each roast’s identity, communicates its ministry partnership, and strengthens the mission‑driven heart of Quiet Harbor Coffee.

Target Market(s)

Churches

Industry/Entity Type

Churches, ministries, Christian’s

Requirements
Must have
• I’d like the design to look like the AI GENERATED image I had made of the packaging. It looks classy and clean.
Should not have
• Colorful palette, silly pictures, cartons, mascots

```html
<!DOCTYPE html>
<html lang="en">
<head>
<meta charset="utf-8">
<title>Quiet Harbor Coffee – Packaging Suite</title>
<link href="https://fonts.googleapis.com/css2?family=Oswald:wght@400;600&display=swap" rel="stylesheet">
<style>
:root{
  --page:#ffffff;
  --cream:#f4ede1;
  --ink:#3a2e27;
  --white:#ffffff;
  --field:#8aa83b;
  --current:#2d7b86;
  --dawn:#df9a2c;
  --rule:#dcdcdc;
}
*{box-sizing:border-box;margin:0;padding:0}
html,body{width:1200px;height:3236px;overflow:hidden;background:var(--page);font-family:"Oswald",sans-serif;color:var(--ink)}
.canvas{position:relative;width:1200px;height:3236px}
.roast-field{--roast:var(--field)}
.roast-current{--roast:var(--current)}
.roast-dawn{--roast:var(--dawn)}

.roast-row{position:absolute;left:0;width:1200px;height:840px}

.wordmark{font-weight:600;color:var(--ink);text-transform:uppercase;text-align:center;line-height:1.05;letter-spacing:.04em}

/* 12 oz bag */
.bag{position:absolute;left:250px;top:60px;width:320px;height:740px;background:var(--cream);border:1px solid #e6dccb}
.bag .wordmark{position:absolute;top:110px;left:0;right:0;font-size:40px}
.bag .band{position:absolute;top:330px;left:0;right:0;height:250px;background:var(--roast);color:var(--white);text-align:center;padding-top:26px}
.name{font-weight:600;text-transform:uppercase;letter-spacing:.02em;line-height:1.15}
.type{font-weight:400;text-transform:uppercase;letter-spacing:.08em;opacity:.92}
.tagline{font-weight:400;text-transform:uppercase;letter-spacing:.05em;line-height:1.3}
.inspired{font-weight:400;text-transform:uppercase;letter-spacing:.08em;opacity:.9}
.rule{display:block;margin:0 auto;background:currentColor;opacity:.7}
.bag .name{font-size:36px}
.bag .type{font-size:17px;margin-top:2px}
.bag .rule{width:40px;height:2px;margin:18px auto}
.bag .tagline{font-size:18px}
.bag .inspired{font-size:12px;margin-top:22px}
.count{text-align:center;color:var(--roast);text-transform:uppercase;line-height:1.2}
.count b{display:block;font-size:30px;font-weight:600}
.count span{display:block;font-size:11px;letter-spacing:.1em}
.bag .count{position:absolute;bottom:70px;left:0;right:0}

/* pod lid */
.lid{position:absolute;border-radius:50%;overflow:hidden;background:var(--cream);border:3px solid #e8e8e8}
.lid .half{position:absolute;left:0;right:0;bottom:0;height:50%;background:var(--roast);color:var(--white);text-align:center}
.roast-row .lid{left:780px;top:60px;width:280px;height:280px}
.roast-row .lid .wordmark{position:absolute;top:38px;left:0;right:0;font-size:26px}
.roast-row .lid .half{padding-top:34px}
.roast-row .lid .name{font-size:28px}
.roast-row .lid .type{font-size:14px}

/* pod box */
.box{position:absolute;left:640px;top:400px;width:440px;height:400px;background:var(--cream);border:1px solid #e6dccb}
.box .wordmark{position:absolute;top:28px;right:40px;font-size:24px;text-align:right}
.box .band{position:absolute;top:116px;left:0;right:0;height:206px;background:var(--roast);color:var(--white);padding:26px 40px}
.box .name{font-size:30px}
.box .type{font-size:14px}
.box .rule{width:36px;height:2px;margin:14px 0}
.box .tagline{font-size:16px}
.box .inspired{font-size:11px;margin-top:14px}
.box .count{position:absolute;left:0;right:0;top:336px}
.box .count b{font-size:22px}
.box .count span{font-size:10px}

.divider{position:absolute;left:0;top:2580px;width:1200px;height:1px;background:var(--rule)}

/* flat lineup */
.lineup .lid{width:150px;height:150px;top:2620px}
.lineup .lid .wordmark{position:absolute;top:22px;left:0;right:0;font-size:14px}
.lineup .lid .half{padding-top:16px}
.lineup .lid .name{font-size:15px}
.lineup .lid .type{font-size:8px}
.panel{position:absolute;top:2820px;width:150px;height:380px;background:var(--cream);border:1px solid #e6dccb}
.panel .wordmark{position:absolute;top:40px;left:0;right:0;font-size:18px}
.panel .band{position:absolute;top:130px;left:0;right:0;height:140px;background:var(--roast);color:var(--white);text-align:center;padding-top:16px}
.panel .name{font-size:17px}
.panel .type{font-size:8px}
.panel .rule{width:20px;height:1px;margin:10px auto}
.panel .tagline{font-size:9px}
.panel .inspired{font-size:6px;margin-top:10px}
.panel .count{position:absolute;bottom:40px;left:0;right:0}
.panel .count b{font-size:16px}
.panel .count span{font-size:6px}
.slot-1{left:345px}.slot-2{left:525px}.slot-3{left:705px}
</style>
</head>
<body>
<main class="canvas">

  <section class="roast-row roast-field" style="top:0">
    <div class="bag">
      <div class="wordmark">Quiet Harbor<br>Coffee</div>
      <div class="band">
        <div class="name">Golden Field</div>
        <div class="type">Light Roast</div>
        <span class="rule"></span>
        <div class="tagline">Brew it. Share it.<br>Fuel the Mission.</div>
        <div class="inspired">Inspired by Harvest Mission Alliance</div>
      </div>
      <div class="count"><b>12</b><span>Single Serve Pods</span></div>
    </div>
    <div class="lid"><div class="wordmark">Quiet Harbor<br>Coffee</div><div class="half"><div class="name">Golden Field</div><div class="type">Light Roast</div></div></div>
    <div class="box">
      <div class="wordmark">Quiet Harbor<br>Coffee</div>
      <div class="band">
        <div class="name">Golden Field</div><div class="type">Light Roast</div>
        <span class="rule"></span>
        <div class="tagline">Brew it. Share it.<br>Fuel the Mission.</div>
        <div class="inspired">Inspired by Harvest Mission Alliance</div>
      </div>
      <div class="count"><b>12</b><span>Single Serve Pods</span></div>
    </div>
  </section>

  <section class="roast-row roast-current" style="top:860px">
    <div class="bag">
      <div class="wordmark">Quiet Harbor<br>Coffee</div>
      <div class="band">
        <div class="name">Deep Current</div>
        <div class="type">Medium Roast</div>
        <span class="rule"></span>
        <div class="tagline">Brew it. Share it.<br>Fuel the Mission.</div>
        <div class="inspired">Inspired by Living Springs Relief</div>
      </div>
      <div class="count"><b>12</b><span>Single Serve Pods</span></div>
    </div>
    <div class="lid"><div class="wordmark">Quiet Harbor<br>Coffee</div><div class="half"><div class="name">Deep Current</div><div class="type">Medium Roast</div></div></div>
    <div class="box">
      <div class="wordmark">Quiet Harbor<br>Coffee</div>
      <div class="band">
        <div class="name">Deep Current</div><div class="type">Medium Roast</div>
        <span class="rule"></span>
        <div class="tagline">Brew it. Share it.<br>Fuel the Mission.</div>
        <div class="inspired">Inspired by Living Springs Relief</div>
      </div>
      <div class="count"><b>12</b><span>Single Serve Pods</span></div>
    </div>
  </section>

  <section class="roast-row roast-dawn" style="top:1720px">
    <div class="bag">
      <div class="wordmark">Quiet Harbor<br>Coffee</div>
      <div class="band">
        <div class="name">New Dawn</div>
        <div class="type">Breakfast Blend</div>
        <span class="rule"></span>
        <div class="tagline">Mission Driven<br>Fueling Global Impact</div>
        <div class="inspired">Inspired by Open Hands Fellowship</div>
      </div>
      <div class="count"><b>12</b><span>Single Serve Pods</span></div>
    </div>
    <div class="lid"><div class="wordmark">Quiet Harbor<br>Coffee</div><div class="half"><div class="name">New Dawn</div><div class="type">Breakfast Blend</div></div></div>
    <div class="box">
      <div class="wordmark">Quiet Harbor<br>Coffee</div>
      <div class="band">
        <div class="name">New Dawn</div><div class="type">Breakfast Blend</div>
        <span class="rule"></span>
        <div class="tagline">Mission Driven<br>Fueling Global Impact</div>
        <div class="inspired">Inspired by Open Hands Fellowship</div>
      </div>
      <div class="count"><b>12</b><span>Single Serve Pods</span></div>
    </div>
  </section>

  <div class="divider"></div>

  <section class="lineup">
    <div class="lid roast-dawn slot-1"><div class="wordmark">Quiet Harbor<br>Coffee</div><div class="half"><div class="name">New Dawn</div><div class="type">Breakfast Blend</div></div></div>
    <div class="lid roast-field slot-2"><div class="wordmark">Quiet Harbor<br>Coffee</div><div class="half"><div class="name">Golden Field</div><div class="type">Light Roast</div></div></div>
    <div class="lid roast-current slot-3"><div class="wordmark">Quiet Harbor<br>Coffee</div><div class="half"><div class="name">Deep Current</div><div class="type">Medium Roast</div></div></div>

    <div class="panel roast-dawn slot-1">
      <div class="wordmark">Quiet Harbor<br>Coffee</div>
      <div class="band"><div class="name">New Dawn</div><div class="type">Breakfast Blend</div><span class="rule"></span><div class="tagline">Mission Driven<br>Fueling Global Impact</div><div class="inspired">Inspired by Open Hands Fellowship</div></div>
      <div class="count"><b>12</b><span>Single Serve Pods</span></div>
    </div>
    <div class="panel roast-field slot-2">
      <div class="wordmark">Quiet Harbor<br>Coffee</div>
      <div class="band"><div class="name">Golden Field</div><div class="type">Light Roast</div><span class="rule"></span><div class="tagline">Brew it. Share it.<br>Fuel the Mission.</div><div class="inspired">Inspired by Harvest Mission Alliance</div></div>
      <div class="count"><b>12</b><span>Single Serve Pods</span></div>
    </div>
    <div class="panel roast-current slot-3">
      <div class="wordmark">Quiet Harbor<br>Coffee</div>
      <div class="band"><div class="name">Deep Current</div><div class="type">Medium Roast</div><span class="rule"></span><div class="tagline">Brew it. Share it.<br>Fuel the Mission.</div><div class="inspired">Inspired by Living Springs Relief</div></div>
      <div class="count"><b>12</b><span>Single Serve Pods</span></div>
    </div>
  </section>

</main>
</body>
</html>
```